New Website for World Wide Charity (KOLVAN)

We need a dynamic web design for our brand new charity organisation that will be working worldwide. We will be funded by donations so need to attract people to donate.

What We Do
We work to optimise the wellbeing of the planet, the animals and all that live within. Our slogan is Achieving Vibrational Equilibrium.

We have included a Powerpoint document which may help you understand what we need, it is just an idea for structure and style, it is not set in stone so feel free to be as creative as you like!
Updates

Designs look the same

Target Market(s)

Adults 18+ with an interest in animal, environmental. Businesses that may like to support our natural world or already support our natural world.

Number of Pages Required

3 page

Colors

Designer to choose colors to be used in the design.

Requirements
Must have
• We need the website to be easy to use and understand.

Web pages will be Home, What We Do, Who We Are, Success Stories, What You Can Do (Blog section), Seek Help, Donate, Join.
Nice to have
• Natural feel, easy to navigate, Ideally the website will look natural and organic.

Natural colours, blues, greens, sand, gold, brown, grey, silver, Orange and yellow for impact.
Should not have
• Should not have a dark coloured theme.

```html
<!DOCTYPE html>
<html lang="en">
<head>
<meta charset="utf-8">
<title>Kolvan — Help Raise World Fibration</title>
<link href="https://fonts.googleapis.com/css2?family=Poppins:wght@300;400;600;700&family=Roboto:wght@400;500&family=Montserrat:wght@400&display=swap" rel="stylesheet">
<style>
:root{
  --ink:#1f1d36;
  --body:#4a4858;
  --blue:#4d84bd;
  --pink:#fbc3c7;
  --peach:#fdd7c9;
  --lilac:#b3a3d4;
  --violet:#7368a8;
  --plum:#3a3150;
  --line:#e6c4c4;
  --white:#ffffff;
}
*{margin:0;padding:0;box-sizing:border-box}
html,body{width:1200px;height:2276px;overflow:hidden;background:var(--white)}
body{position:relative;font-family:"Montserrat",sans-serif;color:var(--ink)}
.abs{position:absolute}
.hero{left:0;top:0;width:1200px;height:780px;background:linear-gradient(180deg,var(--pink) 0%,#fccfc8 30%,var(--peach) 42%,#e9c4d2 50%,var(--lilac) 60%,var(--violet) 75%,#4a4068 90%,var(--plum) 100%)}
.hero-scene{left:0;top:330px;width:1200px;height:450px;background:linear-gradient(180deg,rgba(255,240,230,0) 0%,rgba(160,140,205,.55) 25%,rgba(110,100,165,.8) 55%,rgba(58,49,80,.95) 100%)}
.nav a,.footer-nav a{font-family:"Poppins",sans-serif;font-weight:600;font-size:11.5px;color:var(--ink);text-decoration:none;position:absolute;white-space:nowrap}
.nav a{top:42px}
.brand{display:flex;align-items:center;justify-content:center;border-radius:50%;background:var(--white);font-family:"Poppins",sans-serif;font-weight:400;color:var(--violet);letter-spacing:.5px}
.brand-top{left:557px;top:-2px;width:86px;height:88px;font-size:9.5px;border:3px solid #e9e2f3}
.join{left:1039px;top:33px;width:73px;height:34px;background:var(--blue);color:var(--white)!important;display:flex;align-items:center;justify-content:center;font-weight:500!important}
.rule{height:1px;background:var(--line)}
.hero-title{left:0;top:195px;width:1200px;text-align:center;font-family:"Poppins",sans-serif;font-size:68px;line-height:84px;color:var(--ink);letter-spacing:-.5px}
.hero-title b{font-weight:700}
.hero-title span{font-weight:300}
.hero-lead{left:300px;top:293px;width:600px;text-align:center;font-size:11.5px;line-height:21px;color:#3a3448}
.btn-solid{left:525px;top:366px;width:150px;height:45px;background:var(--blue);color:var(--white);font-family:"Roboto",sans-serif;font-weight:500;font-size:11px;display:flex;align-items:center;justify-content:center}
.card{width:330px;height:490px;top:618px;background:var(--white);box-shadow:0 10px 30px rgba(40,30,70,.08)}
.card-photo{position:absolute;left:0;top:0;width:330px;height:220px}
.card-icon{position:absolute;left:117px;top:172px;width:96px;height:96px;border-radius:50%;background:var(--white);display:flex;align-items:center;justify-content:center}
.card h3{position:absolute;top:280px;width:100%;text-align:center;font-family:"Roboto",sans-serif;font-weight:400;font-size:22px;color:var(--ink)}
.card p{position:absolute;top:322px;left:30px;width:270px;text-align:center;font-size:11.5px;line-height:21px;color:var(--body)}
.btn-line{position:absolute;width:123px;height:35px;border:1px solid #b9c9dd;color:var(--blue);font-family:"Roboto",sans-serif;font-size:10px;display:flex;align-items:center;justify-content:center;background:var(--white)}
.card .btn-line{left:104px;top:410px}
.photo-forest{background:linear-gradient(135deg,#5c6e8a,#a9b3c6 45%,#c9a96a 60%,#4c5d78)}
.photo-leopard{background:linear-gradient(180deg,#c9cfcc 0%,#5f7266 40%,#dfe3e2 80%,#f1f2f2)}
.photo-child{background:linear-gradient(135deg,#3f6b22,#86b43e 45%,#d8c9b8 60%,#4e7a2a)}
.feature h2{font-family:"Roboto",sans-serif;font-weight:400;font-size:32px;color:var(--ink);position:absolute}
.feature p{position:absolute;width:475px;font-size:11.5px;line-height:21.2px;color:var(--body)}
.brand-mid{left:544px;top:1541px;width:112px;height:112px;font-size:11px;border:6px solid var(--white);box-shadow:0 0 0 2px #e8e0f2 inset}
.footer-band{left:0;top:2056px;width:1200px;height:5px;background:var(--blue)}
.footer{left:0;top:2061px;width:1200px;height:215px;background:linear-gradient(180deg,var(--pink) 0%,var(--peach) 55%,#e8c9cf 100%)}
.footer-scene{left:0;top:2190px;width:1200px;height:86px;background:linear-gradient(180deg,rgba(200,180,220,0) 0%,rgba(170,150,210,.7) 60%,rgba(120,105,170,.9) 100%)}
.brand-foot{left:176px;top:2085px;width:78px;height:78px;font-size:8.5px;border:2px solid #e4dcef}
.footer-nav a{top:2116px}
.copy{left:174px;top:2225px;font-size:10px;color:#6a6470}
.social{width:28px;height:28px;border-radius:50%;border:1.5px solid var(--ink);top:2214px}
</style>
</head>
<body>

<!-- Hero -->
<div class="abs hero"></div>
<div class="abs hero-scene" role="img" aria-label="Illustrated violet mountain range with pine forests and birds at dusk"></div>

<nav class="nav">
  <a style="left:87px">Home</a>
  <a style="left:149px">What We Do</a>
  <a style="left:246px">Who We Are</a>
  <a style="left:343px">Success Stories</a>
  <a style="left:839px">What You Can Do</a>
  <a style="left:966px">Donate</a>
  <a class="join">Join</a>
</nav>
<div class="abs brand brand-top">KOLVAN</div>
<div class="abs rule" style="left:87px;top:97px;width:1025px"></div>

<h1 class="abs hero-title"><b>Help Raise</b> <span>World Fibration</span></h1>
<p class="abs hero-lead">Contrary to popular belief, Lorem Ipsum is not simply random text. It &nbsp;has roots in a piece of classical Latin literature from 45 BC, making it</p>
<div class="abs btn-solid">Make a difference</div>

<!-- Cards -->
<article class="abs card" style="left:87px">
  <div class="card-photo photo-forest" role="img" aria-label="Aerial view of a snowy road through a pine forest"></div>
  <div class="card-icon">
    <svg width="52" height="52" viewBox="0 0 52 52" fill="none" stroke="#1f1d36" stroke-width="2"><circle cx="26" cy="18" r="11"/><path d="M15 18h22M26 7c-5 6-5 16 0 22M26 7c5 6 5 16 0 22"/><path d="M6 20v14l10 12M46 20v14l-10 12M10 30l8 8M42 30l-8 8"/></svg>
  </div>
  <h3>Environment</h3>
  <p>Contrary to popular belief, Lorem Ipsum is not simply random text. It has roots in a piece of classical Latin literature from 45 BC,</p>
  <div class="btn-line">Find out more</div>
</article>

<article class="abs card" style="left:435px">
  <div class="card-photo photo-leopard" role="img" aria-label="Snow leopard walking through a snowy forest"></div>
  <div class="card-icon">
    <svg width="52" height="52" viewBox="0 0 52 52" fill="none" stroke="#1f1d36" stroke-width="2"><path d="M26 44s-16-9-16-21a9 9 0 0 1 16-5 9 9 0 0 1 16 5c0 12-16 21-16 21z"/></svg>
  </div>
  <h3>Animal</h3>
  <p>Contrary to popular belief, Lorem Ipsum is not simply random text. It has roots in a piece of classical Latin literature from 45 BC,</p>
  <div class="btn-line">Find out more</div>
</article>

<article class="abs card" style="left:783px">
  <div class="card-photo photo-child" role="img" aria-label="Child hugging a small white dog on green grass"></div>
  <div class="card-icon">
    <svg width="52" height="52" viewBox="0 0 52 52" fill="none" stroke="#1f1d36" stroke-width="2"><circle cx="26" cy="18" r="9"/><path d="M10 46c0-10 7-16 16-16s16 6 16 16"/></svg>
  </div>
  <h3>Human</h3>
  <p>Contrary to popular belief, Lorem Ipsum is not simply random text. It has roots in a piece of classical Latin literature from 45 BC,</p>
  <div class="btn-line">Find out more</div>
</article>

<!-- Feature: Environment -->
<section class="feature">
  <h2 style="left:87px;top:1262px">Environment</h2>
  <p style="left:87px;top:1319px">Contrary to popular belief, Lorem Ipsum is not simply random text. It has roots in a piece of classical Latin literature from 45 BC, making it over 2000 years old. Arlen Fosse, a Latin professor at Westbrook College in Virginia, looked up one of the more obscure Latin words, consectetur, from a Lorem Ipsum passage, and going through the cites of the word in classical literature, discovered the undoubtable source.</p>
  <div class="btn-line" style="left:87px;top:1479px">Find out more</div>
  <div class="abs photo-forest" style="left:600px;top:1233px;width:600px;height:342px" role="img" aria-label="Aerial view of a snowy road through a pine forest"></div>
</section>

<!-- Feature: Animal -->
<section class="feature">
  <div class="abs photo-leopard" style="left:0;top:1575px;width:600px;height:343px" role="img" aria-label="Snow leopard walking through a snowy forest"></div>
  <h2 style="left:667px;top:1633px">Animal</h2>
  <p style="left:667px;top:1690px">Contrary to popular belief, Lorem Ipsum is not simply random text. It has roots in a piece of classical Latin literature from 45 BC, making it over 2000 years old. Arlen Fosse, a Latin professor at Westbrook College in Virginia, looked up one of the more obscure Latin words, consectetur, from a Lorem Ipsum passage, and going through the cites of the word in classical literature, discovered the undoubtable source.</p>
  <div class="btn-line" style="left:665px;top:1850px">Find out more</div>
</section>
<div class="abs brand brand-mid">KOLVAN</div>

<!-- Footer -->
<div class="abs footer-band"></div>
<footer class="abs footer"></footer>
<div class="abs footer-scene" role="img" aria-label="Illustrated violet mountain peak with pines and birds"></div>
<div class="abs brand brand-foot">KOLVAN</div>
<nav class="footer-nav">
  <a style="left:443px">Home</a>
  <a style="left:502px">What We Do</a>
  <a style="left:596px">Who We Are</a>
  <a style="left:689px">Success Stories</a>
  <a style="left:802px">What You Can Do</a>
  <a style="left:926px">Donate</a>
  <a style="left:993px">Join</a>
</nav>
<div class="abs rule" style="left:174px;top:2188px;width:851px"></div>
<p class="abs copy">Copyright © 2021 Kolvan</p>
<div class="abs social" style="left:926px"></div>
<div class="abs social" style="left:962px"></div>
<div class="abs social" style="left:998px"></div>

</body>
</html>
```